Bork Ventures, Inc. Website redesign

Revamp the website, it is old and outdated. www.borkventuresinc.example

Target Market(s)

Information Technology Consulting and Staffing

Coding

Coded - Design and coding required

Number of Pages Required

5+ page

Colors

Designer to choose colors to be used in the design.

Requirements
Must have
• Outlined text boxes just like from the Tolvane.example site. A clean look

```html
<!DOCTYPE html>
<html lang="en">
<head>
<meta charset="utf-8">
<title>Bork Ventures, Inc. — IT Consulting</title>
<link href="https://fonts.googleapis.com/css2?family=Kumbh+Sans:wght@400;600;700;800&family=Raleway:wght@400;500;600;700&display=swap" rel="stylesheet">
<style>
:root{
  --red:#9d1c32;
  --red-dark:#7e1526;
  --ink:#1d1d1f;
  --body:#5b5b5b;
  --grey-bg:#efefef;
  --pink:#f6e6e9;
  --footer:#16171b;
  --white:#ffffff;
}
*{margin:0;padding:0;box-sizing:border-box}
html,body{width:1200px;height:4198px;overflow:hidden}
body{position:relative;font-family:"Raleway",sans-serif;color:var(--ink);background:var(--white)}
.abs{position:absolute}

/* top bar */
.topbar{left:0;top:0;width:1200px;height:41px;background:var(--red);color:#fff;font-size:14px}
.topbar .phone{top:10px;font-weight:700;font-family:"Kumbh Sans",sans-serif;font-size:16px}
.topbar .addr{top:12px;font-size:13px}
/* nav */
.nav{left:0;top:41px;width:1200px;height:83px;background:#fff}
.brand{font-family:"Kumbh Sans",sans-serif;font-weight:800;color:var(--ink);font-size:26px;letter-spacing:1px;white-space:nowrap}
.brand-mark{width:18px;height:18px;background:var(--red);display:inline-block;margin-left:10px;vertical-align:middle}
.menu{left:376px;top:75px;display:flex;gap:26px;font-size:13px;font-weight:600;font-family:"Kumbh Sans",sans-serif}
.menu .on{color:var(--red)}
.search{left:935px;top:61px;width:188px;height:46px;background:#f0f0f0;border-radius:3px;font-size:13px;color:#777;padding:14px 15px}

/* hero */
.hero{left:0;top:124px;width:1200px;height:574px;background:linear-gradient(100deg,#11151c 0%,#263849 45%,#47627a 75%,#2b3a48 100%);clip-path:polygon(0 0,100% 0,100% 446px,600px 574px,0 471px)}
.hero-title{left:77px;top:275px;font-family:"Kumbh Sans",sans-serif;font-weight:800;font-size:48px;line-height:60px;color:#fff}
.hero-sub{left:79px;top:404px;color:#fff;font-size:15px;line-height:27px}
.btn{background:var(--red);color:#fff;font-family:"Kumbh Sans",sans-serif;font-weight:700;font-size:16px;text-align:center;clip-path:polygon(8% 0,100% 0,92% 100%,0 100%)}
.arrow{width:52px;height:52px;border-radius:50%;background:rgba(0,0,0,.45)}

/* welcome */
.eyebrow{left:119px;top:762px;color:var(--red);font-size:15px;letter-spacing:1px;font-weight:500}
.welcome h2{left:116px;top:795px;font-family:"Kumbh Sans",sans-serif;font-size:37px;font-weight:600;line-height:51px}
.welcome p{left:120px;top:910px;width:480px;font-size:13px;line-height:27px;color:var(--body)}
.welcome p a{color:var(--red);font-weight:600;text-decoration:none}
.person{left:668px;top:698px;width:432px;height:448px;background:linear-gradient(180deg,#ffffff 0%,#c7ced3 35%,#5a6872 70%,#2e3a44 100%)}

/* sections */
.grey{left:0;width:1200px;background:var(--grey-bg)}
.sec-title{left:0;width:1200px;text-align:center;font-family:"Kumbh Sans",sans-serif;font-weight:600;font-size:41px}
.sec-sub{left:0;width:1200px;text-align:center;font-size:15px;color:#333}
.card{width:448px;background:#fff;border-bottom:4px solid var(--red)}
.card .img{height:292px}
.card .label{height:61px;padding:0 20px;display:flex;align-items:center;justify-content:space-between;font-family:"Kumbh Sans",sans-serif;font-weight:700;font-size:20px}
.plus{width:42px;height:32px;background:var(--red);color:#fff;font-size:22px;font-weight:400;display:flex;align-items:center;justify-content:center;clip-path:polygon(12% 0,100% 0,88% 100%,0 100%)}

/* strategy */
.strat-p{left:250px;top:2284px;width:700px;text-align:center;font-size:13px;line-height:28px;color:#444}
.strat-center{left:470px;top:2380px;width:260px;height:260px;border-radius:50%;background:radial-gradient(circle,#b8394f 0%,var(--red) 70%)}
.step{width:96px;height:96px;border-radius:50%;background:var(--pink);display:flex;align-items:center;justify-content:center}
.step-label{font-family:"Kumbh Sans",sans-serif;font-weight:700;font-size:18px}

/* news */
.news{width:313px;height:484px;background:#fff}
.news .img{height:218px}
.hex{width:75px;height:76px;background:var(--red);color:#fff;clip-path:polygon(50% 0,100% 25%,100% 75%,50% 100%,0 75%,0 25%);text-align:center;font-family:"Kumbh Sans",sans-serif}
.hex b{display:block;font-size:22px;padding-top:15px;line-height:22px}
.hex span{font-size:12px}
.news h3{left:20px;top:288px;width:280px;font-family:"Kumbh Sans",sans-serif;font-size:16px;line-height:28px;font-weight:700}
.news p{left:19px;top:347px;width:280px;font-size:13px;line-height:27px;color:#777}
.news .more{right:18px;top:437px;color:var(--red);font-weight:700;font-size:15px;font-family:"Kumbh Sans",sans-serif}

/* cta */
.cta{left:0;top:3557px;width:1200px;height:293px;background:linear-gradient(120deg,var(--red-dark),var(--red) 50%,#8e1a2d)}
.cta p{left:0;top:70px;width:1200px;text-align:center;color:#fff;font-family:"Kumbh Sans",sans-serif;font-size:27px;line-height:42px}
.cta .outline{left:513px;top:168px;width:172px;height:56px;border:2px solid #fff;color:#fff;font-size:19px;font-family:"Kumbh Sans",sans-serif;display:flex;align-items:center;justify-content:center}

/* footer */
.footer{left:0;top:3850px;width:1200px;height:348px;background:var(--footer);color:#cfcfcf}
.footer .brand{color:#fff}
.f-about{left:79px;top:102px;width:370px;font-size:13px;line-height:27px}
.social{width:48px;height:48px;border-radius:50%;background:#2b4da8}
.f-head{font-family:"Kumbh Sans",sans-serif;font-weight:700;font-size:18px;color:#fff}
.sitemap{left:527px;top:78px;list-style:none;font-size:13px;line-height:31px}
.sitemap li::before{content:"";display:inline-block;width:5px;height:5px;border-radius:50%;background:var(--red);margin-right:13px;vertical-align:middle}
.dot{width:42px;height:42px;border-radius:50%;background:var(--red);display:flex;align-items:center;justify-content:center}
.f-addr{left:879px;top:72px;font-size:14px;line-height:27px}
.f-phone{left:879px;top:200px;font-family:"Kumbh Sans",sans-serif;font-size:17px;color:#fff}
.f-rule{left:79px;top:285px;width:1042px;height:1px;background:#33343a}
.copy{left:0;top:310px;width:1200px;text-align:center;font-size:12px;color:#999}
</style>
</head>
<body>

<!-- Top bar -->
<div class="abs topbar">
  <svg class="abs" style="left:626px;top:9px" width="24" height="24" viewBox="0 0 24 24"><circle cx="12" cy="12" r="11" fill="none" stroke="#fff" stroke-width="1.5"/><path d="M8 7l2 0 1 3-1.5 1a7 7 0 0 0 3.5 3.5l1-1.5 3 1 0 2c-5 1-10-4-9-9z" fill="#fff"/></svg>
  <span class="abs phone" style="left:661px">301-555-0142</span>
  <svg class="abs" style="left:787px;top:10px" width="14" height="20" viewBox="0 0 14 20"><path d="M7 0a7 7 0 0 1 7 7c0 5-7 13-7 13S0 12 0 7a7 7 0 0 1 7-7z" fill="#fff"/><circle cx="7" cy="7" r="2.5" fill="var(--red)"/></svg>
  <span class="abs addr" style="left:810px">2280 Larkspur Ct Ridgemont, MD 20900</span>
</div>

<!-- Navigation -->
<div class="abs nav"></div>
<div class="abs brand" style="left:77px;top:65px">BORK VENTURES<span class="brand-mark"></span></div>
<nav class="abs menu"><span class="on">HOME</span><span>ABOUT US</span><span>SERVICES</span><span>STRATEGY</span><span>IT NEWS</span><span>CONTACT US</span></nav>
<div class="abs search">Type...</div>
<svg class="abs" style="left:1098px;top:76px" width="16" height="16" viewBox="0 0 16 16"><circle cx="6.5" cy="6.5" r="5" fill="none" stroke="var(--red)" stroke-width="2"/><path d="M10 10l5 5" stroke="var(--red)" stroke-width="2"/></svg>

<!-- Hero -->
<div class="abs hero" role="img" aria-label="Team of IT professionals gathered around glowing digital data screens"></div>
<h1 class="abs hero-title">BORK MISSION<br>INTEGRITY RESULTS</h1>
<p class="abs hero-sub">Bork Ventures, Inc. is an 8(a) innovative and rapidly<br>growing full-service IT consulting firm</p>
<div class="abs btn" style="left:78px;top:473px;width:168px;height:55px;line-height:55px">CONTACT US</div>
<div class="abs arrow" style="left:11px;top:342px"></div>
<svg class="abs" style="left:30px;top:358px" width="12" height="20"><path d="M10 2L2 10l8 8" fill="none" stroke="#fff" stroke-width="1.5"/></svg>
<div class="abs arrow" style="left:1134px;top:342px"></div>
<svg class="abs" style="left:1155px;top:358px" width="12" height="20"><path d="M2 2l8 8-8 8" fill="none" stroke="#fff" stroke-width="1.5"/></svg>

<!-- Welcome -->
<section class="welcome">
  <div class="abs eyebrow">WELCOME TO</div>
  <h2 class="abs">Bringing Thought Leadership<br>&amp; Quality to Every Project</h2>
  <p class="abs">Bork Ventures, Inc. is an 8(a) full-service IT consulting company based in the Washington, DC Metro area. We offer specialized, highly customized technology solutions for our customers located throughout the United States. <a href="#">Learn about our Services now.</a></p>
  <div class="abs btn" style="left:119px;top:1033px;width:171px;height:56px;line-height:56px">LEARN MORE</div>
  <div class="abs person" role="img" aria-label="Consultant holding a laptop and pointing forward"></div>
</section>

<!-- Services -->
<div class="abs grey" style="top:1146px;height:989px"></div>
<h2 class="abs sec-title" style="top:1200px">Services We Provide You</h2>
<p class="abs sec-sub" style="top:1260px">Our people and our process is what makes us successful in providing these services.</p>

<div class="abs card" style="left:140px;top:1312px">
  <div class="img" role="img" aria-label="Network router on a desk" style="background:linear-gradient(160deg,#f3e6c7,#a88c5e 55%,#2c2a26)"></div>
  <div class="label">Hardware / Software Sales<span class="plus">+</span></div>
</div>
<div class="abs card" style="left:611px;top:1312px">
  <div class="img" role="img" aria-label="Technician working at a server rack" style="background:linear-gradient(120deg,#1c2630,#3a4a58 50%,#101820)"></div>
  <div class="label">Professional Services<span class="plus">+</span></div>
</div>
<div class="abs card" style="left:140px;top:1708px">
  <div class="img" role="img" aria-label="Woman touching a glowing circuit display at night" style="background:linear-gradient(110deg,#0f1a2c,#1e3a55 55%,#4b7aa0)"></div>
  <div class="label">Technology Assessment<span class="plus">+</span></div>
</div>
<div class="abs card" style="left:611px;top:1708px">
  <div class="img" role="img" aria-label="Consulting team meeting around a laptop" style="background:linear-gradient(180deg,#dfe3e6,#9aa6b0 55%,#e9ecee)"></div>
  <div class="label">Technology Consulting<span class="plus">+</span></div>
</div>

<!-- Strategy -->
<h2 class="abs sec-title" style="top:2191px">Our Strategy</h2>
<p class="abs sec-sub" style="top:2249px">Your Path to Success</p>
<p class="abs strat-p">Civilian and Federal agencies are facing increased demands driven by the changing economic environment and shifts in the way products and services are sold and delivered.</p>

<div class="abs strat-center" role="img" aria-label="Central brand emblem"></div>

<div class="abs step" style="left:340px;top:2377px"><svg width="46" height="46" viewBox="0 0 46 46" fill="none" stroke="var(--red)" stroke-width="1.6"><rect x="14" y="8" width="24" height="32"/><circle cx="14" cy="18" r="8"/><path d="M19 24l-8 10M20 16h14M22 22h12M20 30h14"/></svg></div>
<div class="abs step-label" style="left:262px;top:2413px">Assess</div>

<div class="abs step" style="left:757px;top:2377px"><svg width="46" height="46" viewBox="0 0 46 46" fill="none" stroke="var(--red)" stroke-width="1.6"><circle cx="23" cy="23" r="19"/><path d="M9 22l8-6 6 3 6-3 8 6-10 9-6-5"/></svg></div>
<div class="abs step-label" style="left:870px;top:2413px">Manage</div>

<div class="abs step" style="left:390px;top:2523px"><svg width="46" height="46" viewBox="0 0 46 46" fill="none" stroke="var(--red)" stroke-width="1.6"><rect x="6" y="8" width="30" height="28"/><path d="M10 16h22M10 22h16M10 28h10"/><circle cx="36" cy="32" r="6"/></svg></div>
<div class="abs step-label" style="left:267px;top:2561px">Recommend</div>

<div class="abs step" style="left:708px;top:2523px"><svg width="46" height="46" viewBox="0 0 46 46" fill="none" stroke="var(--red)" stroke-width="1.6"><rect x="6" y="8" width="34" height="24"/><path d="M18 38h10M23 32v6M12 16h22M12 22h22"/></svg></div>
<div class="abs step-label" style="left:823px;top:2561px">Monitor</div>

<div class="abs step" style="left:550px;top:2650px"><svg width="46" height="46" viewBox="0 0 46 46" fill="none" stroke="var(--red)" stroke-width="1.6"><circle cx="23" cy="21" r="7"/><circle cx="23" cy="21" r="3"/><path d="M6 32l8-4h10l8 4M32 10l6-3 0 8M14 10H8"/></svg></div>
<div class="abs step-label" style="left:552px;top:2762px">Implement</div>

<!-- News -->
<div class="abs grey" style="top:2844px;height:713px"></div>
<h2 class="abs sec-title" style="top:2894px">Latest News</h2>
<p class="abs sec-sub" style="top:2955px">Mission Integrity Results</p>

<article class="abs news" style="left:104px;top:3009px">
  <div class="img" role="img" aria-label="Colleagues reviewing documents at a desk" style="background:linear-gradient(140deg,#c9b08a,#6c7a86 60%,#2b3d58)"></div>
  <div class="abs hex" style="left:15px;top:182px"><b>02</b><span>SEP</span></div>
  <h3 class="abs">Lorem Ipsum is the Simply Dummy Text of the Print Industry</h3>
  <p class="abs">Lorem Ipsum is simply dummy text of the printing and typesetting industry. Lorem Ipsum has been the industry's.</p>
  <span class="abs more">Read More... »</span>
</article>
<article class="abs news" style="left:443px;top:3009px">
  <div class="img" role="img" aria-label="Businessmen shaking hands in an office" style="background:linear-gradient(140deg,#4d5a52,#8c9894 50%,#dfe3e6)"></div>
  <div class="abs hex" style="left:15px;top:182px"><b>03</b><span>SEP</span></div>
  <h3 class="abs">Lorem Ipsum is the Simply Dummy Text of the Print Industry</h3>
  <p class="abs">Lorem Ipsum is simply dummy text of the printing and typesetting industry. Lorem Ipsum has been the industry's.</p>
  <span class="abs more">Read More... »</span>
</article>
<article class="abs news" style="left:782px;top:3009px">
  <div class="img" role="img" aria-label="Woman touching a glowing circuit display at night" style="background:linear-gradient(110deg,#0f1a2c,#1e3a55 55%,#4b7aa0)"></div>
  <div class="abs hex" style="left:15px;top:182px"><b>04</b><span>SEP</span></div>
  <h3 class="abs">Lorem Ipsum is the Simply Dummy Text of the Print Industry</h3>
  <p class="abs">Lorem Ipsum is simply dummy text of the printing and typesetting industry. Lorem Ipsum has been the industry's.</p>
  <span class="abs more">Read More... »</span>
</article>

<!-- Call to action -->
<section class="abs cta">
  <p class="abs">For over 20 + years, we have been providing reliable IT solutions to<br>businesses in the Washington, DC Metro area and beyond.</p>
  <div class="abs outline">CONTACT US</div>
</section>

<!-- Footer -->
<footer class="abs footer">
  <div class="abs brand" style="left:88px;top:44px">BORK VENTURES<span class="brand-mark"></span></div>
  <p class="abs f-about">Bork Ventures, Inc. is an 8(a) full-service IT consulting company based in the Washington, DC Metro area. We offer specialized, highly customized .</p>
  <div class="abs social" style="left:77px;top:190px"></div>
  <div class="abs social" style="left:129px;top:190px"></div>

  <div class="abs f-head" style="left:527px;top:36px">SITEMAP</div>
  <ul class="abs sitemap"><li>Home</li><li>About Us</li><li>Services</li><li>Strategy</li><li>It News</li><li>Contact Us</li></ul>

  <div class="abs f-head" style="left:823px;top:36px">CONTACT US</div>
  <div class="abs dot" style="left:819px;top:70px"><svg width="14" height="20" viewBox="0 0 14 20"><path d="M7 0a7 7 0 0 1 7 7c0 5-7 13-7 13S0 12 0 7a7 7 0 0 1 7-7z" fill="#fff"/><circle cx="7" cy="7" r="2.5" fill="var(--red)"/></svg></div>
  <p class="abs f-addr">Bork Ventures, Inc.<br>2280 Larkspur Ct<br>Ridgemont,<br>&nbsp;MD 20900</p>
  <div class="abs dot" style="left:819px;top:191px"><svg width="18" height="18" viewBox="0 0 24 24"><path d="M5 3l4 0 2 5-2.5 1.5a11 11 0 0 0 6 6L16 13l5 2 0 4C12 21 3 12 5 3z" fill="#fff"/></svg></div>
  <div class="abs f-phone">301-555-0142</div>

  <div class="abs f-rule"></div>
  <p class="abs copy">©Bork Ventures - 2019 All Rights reserved | Policy</p>
</footer>

</body>
</html>
```